Corinnehabbard.com

1. Conceptualization and designing of the site Homepage. The Homepage design will be completely customized and based on your design instructions (i.e. preferred colors, links to reference sites that you want us to take reference from if any etc) and the recently completed logo design.
2. Upon homepage design approval, based on it we will be creating the layout for the other 4 site inner pages (i.e. About page, Contact page, Services page, and Insights (publications, media).
3. Once all the inner page designs are approved, we will get the designs built (will make sure that the site is completely Responsive - works on all devices) within your provided WIX account.
4. We will add the static text and images provided by you to the Home page, About page, Contact page, and the Services page. For the 2 Insights sub-pages, we will add 1-2 sample Publications and Media entries.
once you confirm the total number of required entries for the 2 sub-pages, I will accordingly quote you on the same
5. Integration of a Contact form on the Contact page that will email the filled in details to your mail id.

```html
<!DOCTYPE html>
<html lang="en">
<head>
<meta charset="utf-8">
<title>Corinne Habbard Consulting</title>
<link href="https://fonts.googleapis.com/css2?family=Poppins:wght@300;400;500;600;700&display=swap" rel="stylesheet">
<style>
:root{
  --blue:#0a9be0;
  --red:#e5101b;
  --green:#1f9a35;
  --orange:#f39200;
  --ink:#1c1c1c;
  --muted:#444;
  --black:#000;
  --footer:#111;
  --line:#9a9a9a;
}
*{margin:0;padding:0;box-sizing:border-box}
html,body{width:1200px;height:4874px;overflow:hidden}
body{position:relative;font-family:"Poppins",sans-serif;color:var(--ink);background:#fff}
.photo{position:absolute}

/* top bar */
.topbar-red{position:absolute;left:378px;top:0;width:512px;height:30px;background:var(--red);clip-path:polygon(0 0,100% 0,100% 100%,22px 100%)}
.topbar-green{position:absolute;left:890px;top:0;width:160px;height:30px;background:var(--green)}
.topbar-text{position:absolute;top:7px;color:#fff;font-size:12px;font-weight:500;display:flex;align-items:center;gap:8px;white-space:nowrap}

/* header */
.brand{position:absolute;left:112px;top:20px;display:flex;align-items:center;gap:10px}
.brand-mark{width:44px;height:44px;border-radius:50%;background:var(--blue)}
.brand-name{font-size:14px;font-weight:600;color:var(--blue);line-height:1.2;letter-spacing:.5px}
.nav a{position:absolute;top:58px;font-size:15px;font-weight:500;color:var(--ink);text-decoration:none}
.nav a.active{color:var(--blue)}
.nav .dot{position:absolute;left:619px;top:50px;width:5px;height:5px;border-radius:50%;background:var(--blue)}
.btn-contact{position:absolute;left:977px;top:45px;width:143px;height:46px;background:var(--blue);color:#fff;font-size:15px;font-weight:600;display:flex;align-items:center;justify-content:center}

/* hero */
.hero-photo{left:0;top:104px;width:1200px;height:720px;background:linear-gradient(120deg,#8d8c86 0%,#5f5b57 35%,#3e3a38 60%,#6c6a65 100%)}
.hero-title{position:absolute;right:112px;top:244px;text-align:right;color:#fff;font-size:54px;font-weight:600;line-height:58px;letter-spacing:1px}
.hero-sub{position:absolute;right:112px;top:372px;text-align:right;color:#fff;font-size:21px;font-weight:500;line-height:32px}
.hero-btn{position:absolute;top:463px;height:44px;color:#fff;font-size:15px;font-weight:600;display:flex;align-items:center;justify-content:center}
.hero-btn.start{left:803px;width:150px;background:var(--orange);clip-path:polygon(0 0,100% 0,88% 100%,0 100%)}
.hero-btn.serv{left:938px;width:147px;background:var(--green);clip-path:polygon(12% 0,100% 0,100% 100%,0 100%)}
.slider-dots{position:absolute;left:562px;top:736px;display:flex;gap:6px}
.slider-dots span{width:13px;height:13px;border-radius:50%;border:2px solid #fff}
.slider-dots span.on{border-color:var(--green);background:#fff}
.hero-edge{position:absolute;left:0;top:690px}

/* section heading */
.section-title{position:absolute;left:0;width:1200px;text-align:center;font-size:40px;color:#222}
.section-title .light{font-weight:300}
.section-title b{font-weight:700}

/* services */
.svc-title{position:absolute;font-size:28px;font-weight:600;color:#222;padding-left:14px;border-left:5px solid var(--blue);line-height:36px}
.svc-text{position:absolute;width:474px;font-size:14px;line-height:24.7px;color:var(--muted);text-align:justify}
.btn{position:absolute;width:145px;height:45px;color:#fff;font-size:14px;font-weight:600;display:flex;align-items:center;justify-content:center}
.bar-orange{border-color:var(--orange)}
.bar-blue{border-color:var(--blue)}
.bar-green{border-color:var(--green)}

/* insights */
.insights-sub{position:absolute;left:0;width:1200px;top:2645px;text-align:center;font-size:19px;line-height:31px;color:#333}
.card-photo{top:2738px;width:310px;height:226px;border-radius:10px}
.card-title{position:absolute;top:2990px;width:310px;font-size:21px;font-weight:500;line-height:25px;color:#222}
.card-text{position:absolute;top:3054px;width:300px;font-size:12px;line-height:21px;color:#555}
.card-link{position:absolute;top:3154px;font-size:14px;font-weight:500;color:var(--red);text-decoration:underline}

/* about */
.about-band{position:absolute;left:526px;top:3331px;width:674px;height:475px;background:var(--red)}
.about-title{position:absolute;left:557px;top:3405px;font-size:40px;color:#fff}
.about-title .light{font-weight:300}
.about-title b{font-weight:600}
.about-text{position:absolute;left:557px;top:3470px;width:525px;font-size:14.5px;line-height:24.5px;color:#fff}
.about-btn{background:#fff;color:var(--blue)}

/* contact */
.contact-box{position:absolute;left:112px;top:3904px;width:478px;height:507px;background:var(--black)}
.contact-title{position:absolute;left:191px;top:3978px;font-size:40px;color:#fff}
.contact-title .light{font-weight:400}
.contact-title b{color:var(--orange);font-weight:600}
.c-icon{position:absolute;left:191px;width:42px;height:42px;border-radius:50%;background:#fff;display:flex;align-items:center;justify-content:center}
.c-label{position:absolute;left:257px;font-size:15px;color:#fff;line-height:23px}
.c-label small{font-size:14px;display:block;color:#ddd}
.social{position:absolute;top:4304px;width:42px;height:42px;border-radius:50%}
.field{position:absolute;left:617px;width:460px;border-bottom:1.5px solid var(--line);font-size:13px;color:#777;padding-bottom:14px}

/* footer */
.footer{position:absolute;left:0;top:4510px;width:1200px;height:364px;background:var(--footer)}
.f-brand{position:absolute;left:140px;top:4650px;width:230px;text-align:center}
.f-mark{width:56px;height:56px;border-radius:50%;background:var(--blue);margin:0 auto 12px}
.f-name{font-size:18px;font-weight:600;color:var(--blue);line-height:22px;letter-spacing:.5px}
.f-col{position:absolute;top:4570px}
.f-col h4{font-size:17px;font-weight:600;color:#fff;padding-bottom:10px;position:relative}
.f-col h4::after{content:"";position:absolute;left:0;bottom:0;width:52px;height:2px;background:var(--orange)}
.f-col ul{list-style:none;margin-top:10px}
.f-col li{font-size:12px;color:#ddd;line-height:23px}
.f-rule{position:absolute;left:112px;top:4786px;width:976px;height:2px;background:linear-gradient(90deg,#0a6fb0,var(--blue),#0a6fb0)}
.f-copy{position:absolute;left:0;top:4806px;width:1200px;text-align:center;font-size:13px;color:#ddd}
</style>
</head>
<body>

<!-- top bar -->
<div class="topbar-red"></div>
<div class="topbar-text" style="left:500px">
  <svg width="12" height="14" viewBox="0 0 12 14"><path d="M6 0a5 5 0 0 0-5 5c0 4 5 9 5 9s5-5 5-9a5 5 0 0 0-5-5zm0 7a2 2 0 1 1 0-4 2 2 0 0 1 0 4z" fill="#fff"/></svg>
  1450 Maple Ridge Road, Brookdale, OH 43917, USA
</div>
<div class="topbar-green"></div>
<div class="topbar-text" style="left:910px">
  <svg width="13" height="13" viewBox="0 0 24 24"><path d="M6.6 10.8a15 15 0 0 0 6.6 6.6l2.2-2.2c.3-.3.7-.4 1-.2 1.1.4 2.3.6 3.6.6.6 0 1 .4 1 1V20c0 .6-.4 1-1 1A17 17 0 0 1 3 4c0-.6.4-1 1-1h3.5c.6 0 1 .4 1 1 0 1.3.2 2.5.6 3.6.1.3 0 .7-.2 1z" fill="#fff"/></svg>
  1-800-555-0142
</div>

<!-- header -->
<div class="brand">
  <div class="brand-mark"></div>
  <div class="brand-name">CORINNE HABBARD<br>CONSULTING</div>
</div>
<nav class="nav">
  <span class="dot"></span>
  <a class="active" style="left:600px">Home</a>
  <a style="left:678px">About us</a>
  <a style="left:776px">Insights</a>
  <a style="left:869px">Services</a>
</nav>
<div class="btn-contact">Contact Us</div>

<!-- hero -->
<div class="photo hero-photo" role="img" aria-label="Team of consultants gathered around a laptop in a bright office"></div>
<div class="hero-title">CORINNE HABBARD<br>CONSULTING</div>
<div class="hero-sub">Perspiciatis unde omnis iste natus error sit<br>voluptatem accusantium doloremae</div>
<div class="hero-btn start">Get Started</div>
<div class="hero-btn serv">Our Services</div>
<div class="slider-dots"><span></span><span class="on"></span><span></span><span></span></div>
<svg class="hero-edge" width="1200" height="200" viewBox="0 0 1200 200">
  <polygon points="0,60 293,12 600,125 922,12 1200,70 1200,200 0,200" fill="#fff"/>
  <polyline points="0,56 293,8 600,121 922,8 1200,66" fill="none" stroke="#0a9be0" stroke-width="12"/>
  <polyline points="0,74 293,28 600,140 922,28 1200,84" fill="none" stroke="#e8e8e8" stroke-width="3"/>
  <polygon points="600,110 630,127 630,163 600,180 570,163 570,127" fill="#e5101b"/>
  <rect x="592" y="130" width="16" height="24" rx="8" fill="none" stroke="#fff" stroke-width="2"/>
  <line x1="600" y1="135" x2="600" y2="141" stroke="#fff" stroke-width="2"/>
  <polyline points="596,160 600,164 604,160" fill="none" stroke="#fff" stroke-width="1.5"/>
</svg>

<!-- services -->
<h2 class="section-title" style="top:948px"><span class="light">Our</span> <b>Services</b></h2>

<div class="photo" style="left:606px;top:1063px;width:594px;height:480px;background:linear-gradient(135deg,#7b6f62,#5a5149 50%,#a59b8f);clip-path:polygon(48px 0,100% 0,100% 100%,0 100%)" role="img" aria-label="Consultant presenting at a whiteboard to a seated team"></div>
<h3 class="svc-title bar-orange" style="left:112px;top:1133px">Strategy Consulting</h3>
<p class="svc-text" style="left:112px;top:1190px">Jasrspiciatis unde omnis istasdse natus error asesit voluptatem accusantium doloremque laudantium, totam remses aperiam, eaque ipsa quae asedb illo inventore veritatis et quasi architecto beatae vitae dictasse susaesnt explicabo. Nemo enim ipsam voluptatem quia voluptas sit aspernatur auset odit aut fugit, sed quia consequuntur magni dolores eos qui ratione voluptatem sequi nesciunt. Neque porro quisquam est, qui dolorem</p>
<div class="btn" style="left:115px;top:1393px;background:var(--orange)">Learn More</div>

<div class="photo" style="left:0;top:1543px;width:606px;height:478px;background:linear-gradient(135deg,#3a3a3c,#6d6c6a 50%,#cfcac2)" role="img" aria-label="Colleagues meeting around a white table in a modern office"></div>
<h3 class="svc-title bar-orange" style="left:623px;top:1655px">Management Consulting</h3>
<p class="svc-text" style="left:623px;top:1716px">Jasrspiciatis unde omnis istasdse natus error asesit voluptatem accusantium doloremque laudantium, totam remses aperiam, eaque ipsa quae asedb illo inventore veritatis et quasi architecto beatae vitae dictasse susaesnt explicabo. Nemo enim ipsam voluptatem quia voluptas sit aspernatur auset odit aut fugit, sed quia consequuntur magni dolores eos qui ratione voluptatem sequi nesciunt. Neque porro quisquam est, qui dolorem</p>
<div class="btn" style="left:625px;top:1940px;background:var(--blue)">Learn More</div>

<div class="photo" style="left:606px;top:2021px;width:594px;height:481px;background:linear-gradient(135deg,#b9aea0,#4b3d33 45%,#2c2522);clip-path:polygon(0 0,100% 0,100% 100%,48px 100%)" role="img" aria-label="Business team discussing around a laptop at a meeting table"></div>
<h3 class="svc-title bar-green" style="left:112px;top:2117px">Financial Consulting</h3>
<p class="svc-text" style="left:112px;top:2170px">Jasrspiciatis unde omnis istasdse natus error asesit voluptatem accusantium doloremque laudantium, totam remses aperiam, eaque ipsa quae asedb illo inventore veritatis et quasi architecto beatae vitae dictasse susaesnt explicabo. Nemo enim ipsam voluptatem quia voluptas sit aspernatur auset odit aut fugit, sed quia consequuntur magni dolores eos qui ratione voluptatem sequi nesciunt. Neque porro quisquam est, qui dolorem</p>
<div class="btn" style="left:115px;top:2370px;background:var(--red)">Learn More</div>

<!-- insights -->
<h2 class="section-title" style="top:2578px"><b>Insights</b></h2>
<p class="insights-sub">Perspiciatis unde omnis iste natus error sit voluptatem accusantium doloremque<br>laudantium totam rem aperiam, eaque ipsa quae ab illo inventore</p>

<div class="photo card-photo" style="left:112px;background:linear-gradient(135deg,#cfc7bb,#8c7d6c 55%,#e6e1d9)" role="img" aria-label="Team working together at a long office table"></div>
<h3 class="card-title" style="left:112px">Perspiciatis unde omnis iste natus error sit.</h3>
<p class="card-text" style="left:112px">Saerspiciatis unde omnis iste natus error sit voluptatem accusan tium doloremque laudantiumotam rem aperiameaque ipaefdsa quae ab illo inventore veritatiset.</p>
<span class="card-link" style="left:112px">Learn More</span>

<div class="photo card-photo" style="left:445px;background:linear-gradient(135deg,#e3e1dc,#9a9388 55%,#5c5750)" role="img" aria-label="Executives in a meeting around a wooden conference table"></div>
<h3 class="card-title" style="left:445px">Perspiciatis unde omnis iste natus error sit.</h3>
<p class="card-text" style="left:445px">Saerspiciatis unde omnis iste natus error sit voluptatem accusan tium doloremque laudantiumotam rem aperiameaque ipaefdsa quae ab illo inventore veritatiset.</p>
<span class="card-link" style="left:445px">Learn More</span>

<div class="photo card-photo" style="left:778px;background:linear-gradient(135deg,#6f8ca6,#34465a 55%,#9aa9b6)" role="img" aria-label="Presenter leading a discussion with colleagues in a glass office"></div>
<h3 class="card-title" style="left:778px">Perspiciatis unde omnis iste natus error sit.</h3>
<p class="card-text" style="left:778px">Saerspiciatis unde omnis iste natus error sit voluptatem accusan tium doloremque laudantiumotam rem aperiameaque ipaefdsa quae ab illo inventore veritatiset.</p>
<span class="card-link" style="left:778px">Learn More</span>

<div class="btn" style="left:528px;top:3198px;background:var(--blue)">View All</div>

<!-- about -->
<div class="photo" style="left:0;top:3331px;width:526px;height:475px;background:linear-gradient(90deg,#d9d2c6,#5b2b20 35%,#6a3124 60%,#2a3156 85%,#d7d0c4)" role="img" aria-label="Consultant standing in a formal hall between two flags"></div>
<div class="about-band"></div>
<h2 class="about-title"><span class="light">About</span> <b>Us</b></h2>
<p class="about-text">Jasrspiciatis undae omnis istasdse natus erkaseiirar asesit voluptatem accusantium doloremque laudantium, totam remses aperiam, eaque ipsa quae asedb illo inventore veritatis et quasi architecto beatae vitae dictasse susaesnt explicabo. Nemokseio enim ipsam voluptatem quia voluptas sit aspernatur auset odit auksat fugit, sed quia consequuntur magni dolores eos qui ratione voluptatem sequi nesciunt. Neque porro quisquam est, qui dolorem.</p>
<div class="btn about-btn" style="left:560px;top:3680px">Learn More</div>

<!-- contact -->
<div class="contact-box"></div>
<h2 class="contact-title"><span class="light">Contact</span> <b>Us</b></h2>

<div class="c-icon" style="top:4052px">
  <svg width="16" height="20" viewBox="0 0 12 14"><path d="M6 0a5 5 0 0 0-5 5c0 4 5 9 5 9s5-5 5-9a5 5 0 0 0-5-5zm0 7a2 2 0 1 1 0-4 2 2 0 0 1 0 4z" fill="#1f9a35"/></svg>
</div>
<div class="c-label" style="top:4052px"><small>Address</small>1450 Maple Ridge Road, Brookdale,<br>OH 43917, USA</div>

<div class="c-icon" style="top:4150px">
  <svg width="20" height="20" viewBox="0 0 24 24"><path d="M6.6 10.8a15 15 0 0 0 6.6 6.6l2.2-2.2c.3-.3.7-.4 1-.2 1.1.4 2.3.6 3.6.6.6 0 1 .4 1 1V20c0 .6-.4 1-1 1A17 17 0 0 1 3 4c0-.6.4-1 1-1h3.5c.6 0 1 .4 1 1 0 1.3.2 2.5.6 3.6.1.3 0 .7-.2 1z" fill="#0a9be0"/></svg>
</div>
<div class="c-label" style="top:4143px"><small>Call Us</small>1-800-555-0142</div>

<div class="c-icon" style="top:4225px">
  <svg width="20" height="16" viewBox="0 0 20 16"><rect x="1" y="1" width="18" height="14" rx="1.5" fill="none" stroke="#e5101b" stroke-width="2"/><polyline points="1,2 10,9 19,2" fill="none" stroke="#e5101b" stroke-width="2"/></svg>
</div>
<div class="c-label" style="top:4217px"><small>Email</small>info@corinnehabbard.com</div>

<span class="social" style="left:191px;background:var(--blue)" role="img" aria-label="Social profile link"></span>
<span class="social" style="left:246px;background:var(--green)" role="img" aria-label="Social profile link"></span>
<span class="social" style="left:301px;background:var(--orange)" role="img" aria-label="Social profile link"></span>

<div class="field" style="top:3980px;padding-left:20px">Your Name</div>
<div class="field" style="top:4040px;padding-left:20px">Email</div>
<div class="field" style="top:4100px;padding-left:20px">Phone Number</div>
<div class="field" style="top:4160px;height:96px;padding-left:20px">Message</div>
<div class="btn" style="left:623px;top:4288px;background:var(--red)">Submit</div>

<!-- footer -->
<footer class="footer"></footer>
<div class="f-brand">
  <div class="f-mark"></div>
  <div class="f-name">CORINNE HABBARD<br>CONSULTING</div>
</div>
<div class="f-col" style="left:524px">
  <h4>Quick Links</h4>
  <ul><li>Home</li><li>About us</li><li>Insights</li><li>Services</li><li>Contact Us</li></ul>
</div>
<div class="f-col" style="left:717px">
  <h4>Links</h4>
  <ul><li>Copyright</li><li>Terms of Use</li><li>Privacy Policy</li><li>Accessibility</li><li>Sitemap</li><li>Contact Us</li></ul>
</div>
<div class="f-col" style="left:895px">
  <h4>Support</h4>
  <ul><li>Team</li><li>About Us</li><li>Careers</li><li>Our Values</li><li>Data Security</li></ul>
</div>
<div class="f-rule"></div>
<p class="f-copy">© 2024. All rights reserved.</p>

</body>
</html>
```